Redesign Of Current Landing Page

I need to redesign this landing page https://www.brightlanepromo.biz/?page=landing&landing=23 (Please do not opt in because when you do it will show you the home page. Please clear your cookies before going to this url above to view the 1 page landing page.)

Please use my updated website as a reference for colors and logo.
http://sitecradlewerk.com/dh/bpq/index.html

I would like the call to action to be a button that opens into a lead form...

Button would be "Download Samples"

Target Market(s)

small business owners

Industry/Entity Type

Marketing

Number of Pages Required

1 page

Colors

Designer to choose colors to be used in the design.

Requirements
Must have
• must be full responsive on all devices
Nice to have
• must have a legitimate professional apeal to it
Should not have
• open

```html
<!DOCTYPE html>
<html lang="en">
<head>
<meta charset="utf-8">
<title>Brightlane Promo Group – Landing</title>
<link rel="stylesheet" href="https://fonts.googleapis.com/css2?family=Mulish:wght@400;600;700&family=Open+Sans:ital,wght@0,400;0,600;1,400&display=swap">
<style>
:root{
  --blue:#0a66c2;
  --blue-deep:#0b4fa8;
  --orange:#f7a21b;
  --orange-dark:#ee8d0a;
  --ink:#222;
  --muted:#7a7a7a;
  --line:#d9d9d9;
  --dark-band:#2a2420;
  --white:#fff;
}
*{box-sizing:border-box;margin:0;padding:0}
html,body{width:1200px;height:3136px;overflow:hidden}
body{font-family:"Open Sans",Arial,sans-serif;color:var(--ink);background:var(--white)}
.section{position:relative;width:1200px;overflow:hidden}
.center{text-align:center}
.heading{font-family:"Mulish",Arial,sans-serif;font-weight:600;letter-spacing:.5px}
.rule{display:block;margin:14px auto 0;width:180px;height:2px;background:var(--line);position:relative}
.rule::after{content:"";position:absolute;left:62px;top:-1px;width:56px;height:4px;background:var(--blue-deep)}
.btn{display:inline-block;font-family:"Mulish",Arial,sans-serif;font-weight:700;font-size:14px;text-transform:uppercase;text-decoration:none;border-radius:3px}
.btn-orange{background:linear-gradient(var(--orange),var(--orange-dark));color:var(--white)}
.btn-blue{background:var(--blue);color:var(--white)}

/* header */
.site-header{height:96px;display:flex;align-items:center;justify-content:space-between;padding:0 120px 0 122px}
.brand{display:flex;align-items:center;gap:10px;font-family:"Mulish",Arial,sans-serif;font-weight:700;font-size:30px;color:var(--blue-deep);letter-spacing:1px}
.brand-dot{width:34px;height:34px;border-radius:50%;background:var(--blue-deep)}
.main-nav{display:flex;gap:24px}
.main-nav a{font-family:"Mulish",Arial,sans-serif;font-size:17px;color:#333;text-decoration:none;text-transform:uppercase}
.main-nav a.active{color:var(--blue)}

/* hero */
.hero{height:580px;background:linear-gradient(120deg,#2b2218 0%,#5a4430 35%,#8b6d4e 55%,#3a2e24 80%,#1f1a16 100%);color:var(--white)}
.hero-photo{position:absolute;inset:0}
.hero-content{position:absolute;left:0;right:0;top:214px;text-align:center}
.hero-title{font-family:"Mulish",Arial,sans-serif;font-weight:700;font-size:38px;letter-spacing:.5px}
.hero-sub{font-family:"Mulish",Arial,sans-serif;font-weight:700;font-size:23px;margin-top:4px}
.btn-outline{margin-top:26px;border:2px solid var(--white);color:var(--white);padding:11px 36px;font-size:17px;border-radius:0}
.slider-dots{position:absolute;left:0;right:0;top:540px;display:flex;justify-content:center;gap:8px}
.slider-dots span{width:14px;height:14px;border-radius:50%;background:var(--white)}
.slider-dots span.current{background:transparent;border:2px solid var(--white)}

/* imagine */
.imagine{height:447px;padding-top:62px}
.imagine .heading{font-size:33px;color:var(--blue);font-weight:600}
.imagine .rule{width:136px;margin-top:8px}
.imagine .rule::after{left:40px}
.imagine-copy{width:860px;margin:36px auto 0;font-size:13.5px;line-height:25px;color:var(--muted)}
.imagine-copy p+p{margin-top:16px}
.imagine .btn-orange{margin-top:28px;padding:13px 28px}

/* why */
.why{height:507px;background:linear-gradient(100deg,#1e1a17 0%,#3b332c 40%,#4a4038 60%,#221d19 100%);color:var(--white);padding-top:60px}
.why .heading{font-size:25px;font-weight:600}
.why .rule{width:470px;background:rgba(255,255,255,.35)}
.why .rule::after{display:none}
.benefit-grid{position:absolute;left:118px;top:163px;display:grid;grid-template-columns:328px 326px 330px;row-gap:62px}
.benefit{display:flex;gap:16px}
.benefit-icon{flex:none;width:92px;height:92px;border-radius:50%;background:var(--blue);display:flex;align-items:center;justify-content:center}
.benefit h3{font-family:"Mulish",Arial,sans-serif;font-weight:600;font-size:16.5px;line-height:21px;margin-top:6px}
.benefit p{font-size:10px;line-height:15px;color:#cfcfcf;margin-top:8px;width:190px}

/* how */
.how{height:505px;padding-top:60px}
.how .heading{font-size:27px;color:var(--ink)}
.how .rule{width:226px;margin-top:12px}
.how .rule::after{left:85px}
.how-photo{position:absolute;left:117px;top:142px;width:415px;height:274px;background:linear-gradient(180deg,#4e9be0 0%,#a9d2f2 40%,#3f8a3a 60%,#1aa0b8 80%,#0d6e94 100%)}
.how-copy{position:absolute;left:562px;top:132px;width:520px;font-size:13.8px;line-height:25px;color:var(--muted)}
.how-copy p+p{margin-top:20px}
.how .btn-blue{position:absolute;left:562px;top:378px;padding:12px 28px;font-size:14px}

/* testimonials */
.testimonials{height:455px;background:linear-gradient(180deg,#c9d8e4 0%,#e7eef3 50%,#dfe3e4 100%)}
.testimonials-bg{position:absolute;inset:0}
.testimonials .heading{position:absolute;left:0;right:0;top:45px;font-size:27px}
.testimonials .rule{width:200px;margin-top:10px}
.testimonials .rule::after{left:72px}
.quote-card{position:absolute;left:283px;top:143px;width:642px;height:215px;background:var(--white);box-shadow:0 2px 6px rgba(0,0,0,.15);padding:52px 44px 0;text-align:center;font-style:italic;font-size:13px;line-height:23px;color:#555}
.quote-badge{position:absolute;left:572px;top:110px;width:58px;height:58px;border-radius:50%;background:var(--blue-deep);display:flex;align-items:center;justify-content:center;color:var(--white);font-family:Georgia,serif;font-size:40px;font-weight:700;line-height:1;padding-top:14px}
.author{position:absolute;left:0;right:0;top:375px;text-align:center;font-family:"Mulish",Arial,sans-serif;color:#555}
.author strong{display:block;font-size:16px;font-weight:600}
.author span{font-size:12px}

/* download */
.download{height:350px;background:linear-gradient(160deg,#0a4ea8 0%,#1a6fd0 40%,#0c5fc2 70%,#0a3f8f 100%);color:var(--white);padding-top:86px}
.download .heading{font-size:27px;font-weight:600}
.download .rule{width:90px;background:transparent;margin-top:10px}
.download .rule::after{left:22px;background:var(--white)}
.download p{width:720px;margin:16px auto 0;font-size:16px;line-height:26px}
.download .btn-orange{margin-top:20px;padding:12px 24px;font-size:16px;font-weight:600}

/* footer */
.site-footer{height:196px;padding-top:52px;text-align:center}
.footer-nav{display:flex;justify-content:center;gap:23px}
.footer-nav a{font-family:"Mulish",Arial,sans-serif;font-size:16px;color:#333;text-decoration:none;text-transform:uppercase}
.copyright{margin-top:10px;font-size:14px;color:var(--muted)}
.social{display:flex;justify-content:center;gap:6px;margin-top:22px}
.social span{width:30px;height:30px;border-radius:50%;border:2px solid var(--blue-deep)}
</style>
</head>
<body>

<header class="site-header">
  <div class="brand"><span class="brand-dot"></span>BLPG</div>
  <nav class="main-nav">
    <a href="#" class="active">Home</a>
    <a href="#">About Us</a>
    <a href="#">Features</a>
    <a href="#">How It Works</a>
    <a href="#">Download Samples</a>
    <a href="#">Contact</a>
  </nav>
</header>

<section class="section hero">
  <div class="hero-photo" role="img" aria-label="Luxury hotel lobby with a sweeping spiral staircase and warm lighting"></div>
  <div class="hero-content">
    <h1 class="hero-title">ATTRACT MORE CUSTOMERS</h1>
    <p class="hero-sub">WHO SPEND MORE MONEY WITH YOUR BUSINESS MORE OFTEN!</p>
    <a href="#" class="btn btn-outline">Read More</a>
  </div>
  <div class="slider-dots"><span class="current"></span><span></span><span></span><span></span></div>
</section>

<section class="section imagine center">
  <h2 class="heading">IMAGINE</h2>
  <span class="rule"></span>
  <div class="imagine-copy">
    <p>being able to create exciting give away promotions that will boost your sales without ever having to worry about cost.</p>
    <p>Brightlane Promo Group, Inc. provides high-perceived value promotional incentives to businesses that want to advertise an exciting Give Away that will instantly attract more customers from your existing advertising efforts.</p>
    <p>Your business can give away incentive certificates that are redeemable for luxury hotel &amp; resort stays with airfare included, cruises, cash for gas, groceries, dining and even electronic goods.</p>
  </div>
  <a href="#" class="btn btn-orange">Read More</a>
</section>

<section class="section why">
  <div class="center">
    <h2 class="heading">WHY OFFER INCENTIVES TO CUSTOMERS?</h2>
    <span class="rule"></span>
  </div>
  <div class="benefit-grid">
    <div class="benefit">
      <div class="benefit-icon"><svg width="40" height="34" viewBox="0 0 40 34" fill="none" stroke="#fff" stroke-width="3"><path d="M2 2v30h36"/><path d="M8 24l9-10 7 6 12-13"/></svg></div>
      <div><h3>Increase Responses From<br>Your Existing Ads</h3><p>Proin nulla arcu nonummy luctus dictum eget fermentum et lorem Nunc porta</p></div>
    </div>
    <div class="benefit">
      <div class="benefit-icon"><svg width="36" height="44" viewBox="0 0 36 44" fill="none" stroke="#fff" stroke-width="2.5" stroke-linejoin="round"><path d="M18 2l4.5 9.5 10 1.2-7.4 7 1.9 10L18 25l-9 4.7 1.9-10-7.4-7 10-1.2z"/><path d="M14 30v10M22 30v10M10 42h16"/></svg></div>
      <div><h3>Build Brand Awareness<br>and Trust</h3><p>Proin nulla arcu nonummy luctus dictum eget fermentum et lorem Nunc porta</p></div>
    </div>
    <div class="benefit">
      <div class="benefit-icon"><svg width="40" height="40" viewBox="0 0 40 40" fill="#fff"><path d="M37 3C26 3 18 10 13 19l8 8c9-5 16-13 16-24z"/><path d="M12 20l-7 1-3 5 8-1zM20 28l-1 7-5 3 1-8z"/><path d="M9 27l4 4-7 5z"/></svg></div>
      <div><h3>Boost Repeat and<br>Referral Business-</h3><p>Proin nulla arcu nonummy luctus dictum eget fermentum et lorem Nunc porta</p></div>
    </div>
    <div class="benefit">
      <div class="benefit-icon"><svg width="38" height="38" viewBox="0 0 38 38" fill="none" stroke="#fff" stroke-width="5" stroke-linecap="round"><path d="M6 32l15-15"/><circle cx="27" cy="11" r="6" stroke-width="4"/></svg></div>
      <div><h3>1 Sales Closing Tool -<br>Gift w/ Purchase</h3><p>Proin nulla arcu nonummy luctus dictum eget fermentum et lorem Nunc porta</p></div>
    </div>
    <div class="benefit">
      <div class="benefit-icon"><svg width="46" height="30" viewBox="0 0 46 30" fill="#fff"><circle cx="23" cy="7" r="6"/><circle cx="9" cy="10" r="4.5"/><circle cx="37" cy="10" r="4.5"/><path d="M12 30c0-9 5-15 11-15s11 6 11 15z"/><path d="M0 28c0-7 4-12 9-12 2 0 3 1 4 1-2 3-3 7-3 11zM46 28c0-7-4-12-9-12-2 0-3 1-4 1 2 3 3 7 3 11z"/></svg></div>
      <div><h3>Insure The Sale Over<br>Your Competition</h3><p>Proin nulla arcu nonummy luctus dictum eget fermentum et lorem Nunc porta</p></div>
    </div>
    <div class="benefit">
      <div class="benefit-icon"><svg width="40" height="38" viewBox="0 0 40 38" fill="none" stroke="#fff" stroke-width="2.5"><ellipse cx="20" cy="8" rx="14" ry="5"/><path d="M6 8v7c0 3 6 5 14 5s14-2 14-5V8M6 15v7c0 3 6 5 14 5s14-2 14-5v-7M6 22v7c0 3 6 5 14 5s14-2 14-5v-7"/></svg></div>
      <div><h3>Improve<br>Retention Rates</h3><p>Proin nulla arcu nonummy luctus dictum eget fermentum et lorem Nunc porta</p></div>
    </div>
  </div>
</section>

<section class="section how">
  <div class="center">
    <h2 class="heading">HOW CAN WE DO IT?</h2>
    <span class="rule"></span>
  </div>
  <div class="how-photo" role="img" aria-label="Tropical resort pool with palm trees, sun loungers and umbrellas under a blue sky"></div>
  <div class="how-copy">
    <p>We help fill empty rooms for thousands of hotels and resorts in hundreds of destinations around the world as well as the major cruise lines. Hotels and resorts are rarely full so when we place someone in their empty rooms, they end up making it up when travelers spend money on room service, spa services, eat at their in-house restaurants, casino and take advantage of other amenities that drive revenue.</p>
    <p>We also help over 18,000 restaurants, electronic manufacturers, the major gas companies and top grocery chains in the U.S and Canada increase brand awareness as well as increase customer loyalty.</p>
  </div>
  <a href="#" class="btn btn-blue">Read More</a>
</section>

<section class="section testimonials">
  <div class="testimonials-bg" role="img" aria-label="Bright seaside terrace with white columns, lounge chairs and trees, softly faded"></div>
  <div class="center heading-wrap">
    <h2 class="heading">TESTIMONIALS<span class="rule"></span></h2>
  </div>
  <div class="quote-card">I began using your incentives two years ago to boost lead generation efforts. I have experienced a 63% increase in lead captures. And, even more importantly, my sales have increased as well. The ability to offer unlimited certificates and not having to pay for each certificate I give away is perhaps the best feature of the program, but having the flexibility to email or print certificates for my customers is also wonderful. I even use your html banners to automate my promotions right on my website!</div>
  <div class="quote-badge">&ldquo;</div>
  <div class="author"><strong>DALE R.</strong><span>CEDARBROOK, TN</span></div>
</section>

<section class="section download center">
  <h2 class="heading">WANT TO OUR DOWNLOAD SAMPLES</h2>
  <span class="rule"></span>
  <p>sociosqu ad litora torquent per conubia nostra per inceptos hymenaeos Proin nulla arcu nonummy luctus dictum eget fermentum et lorem</p>
  <a href="#" class="btn btn-orange">Download Samples</a>
</section>

<footer class="site-footer">
  <nav class="footer-nav">
    <a href="#">Home</a><a href="#">About Us</a><a href="#">Features</a><a href="#">How It Works</a><a href="#">Download Samples</a><a href="#">Contact</a>
  </nav>
  <p class="copyright">© 2017 Company Name &nbsp;All right reserved &nbsp;Term of Use</p>
  <div class="social"><span></span><span></span><span></span><span></span></div>
</footer>

</body>
</html>
```